BQR, LLC Original

I need a business card design for a new company in Gaithersburg, MD. Though the name of the company is Wiremasters Of Northfield (BQR) we specialize in commercial kitchen ventilation systems as a complete turnkey project or as a service provider. We can design the entire system including the hoods, fans, ductwork, and fire system. We also specialize in fire alarm service, design, install and inspection. We are experts on any Ventaro Dynamics equipment including Pulsar VXM, Pulsar Canopies, EMS controls, Standard controls, PCU filtration and Make-up Air units with heaters and cooling. We can repair/retrofit old water wash hood systems as well. We are experts with local code requirements and upgrades.

Industry/Entity Type

Business

Contact Information for Business Card

Dale Pruitt, Wiremasters Of Northfield, LLC; 240-555-0187 Cell, Millbrook, MD 20990. Dalep@wiremastersnorthfield.example

```html
<!DOCTYPE html>
<html lang="en">
<head>
<meta charset="utf-8">
<title>BQR, LLC Business Card</title>
<link rel="stylesheet" href="https://fonts.googleapis.com/css2?family=Cinzel:wght@400;600&family=Arimo:wght@400&display=swap">
<style>
  :root {
    --yellow: #f2dc1e;
    --black: #050505;
    --white: #ffffff;
    --stage: #e9e6e1;
  }
  html, body {
    margin: 0;
    width: 1200px;
    height: 960px;
    overflow: hidden;
    background: var(--stage);
  }
  .card {
    position: absolute;
    left: 250px;
    width: 700px;
    height: 400px;
    overflow: hidden;
    box-shadow: 0 6px 18px rgba(0,0,0,0.18);
  }
  .card--front { top: 50px; background: var(--yellow); }
  .card--back { top: 500px; background: var(--black); }

  /* front */
  .front__brand {
    position: absolute;
    left: 0; right: 0; top: 90px;
    text-align: center;
    font-family: "Cinzel", serif;
    font-weight: 600;
    font-size: 92px;
    line-height: 1;
    color: var(--white);
    letter-spacing: 4px;
  }
  .front__rule {
    position: absolute;
    left: 0; right: 0; top: 262px;
    height: 6px;
    background: var(--white);
  }
  .front__band {
    position: absolute;
    left: 0; right: 0; top: 268px; bottom: 0;
    background: var(--black);
  }
  .front__name {
    position: absolute;
    right: 48px; top: 50px;
    font-family: "Cinzel", serif;
    font-size: 24px;
    color: var(--white);
    letter-spacing: 1px;
    white-space: nowrap;
  }

  /* back */
  .back__brand {
    position: absolute;
    left: 60px; top: 100px;
    font-family: "Cinzel", serif;
    font-weight: 600;
    font-size: 76px;
    line-height: 1;
    color: var(--white);
    letter-spacing: 3px;
  }
  .back__contact {
    position: absolute;
    right: 36px; top: 40px;
    margin: 0; padding: 0;
    list-style: none;
    font-family: "Arimo", sans-serif;
    font-size: 16px;
    line-height: 24px;
    color: var(--white);
    text-align: right;
  }
  .back__contact li { display: flex; justify-content: flex-end; align-items: center; gap: 10px; white-space: nowrap; }
  .back__contact svg { width: 11px; height: 11px; fill: var(--yellow); flex: none; }
  .back__footer {
    position: absolute;
    left: 0; bottom: 0;
    width: 700px; height: 130px;
  }
  .back__person {
    position: absolute;
    left: 46px; bottom: 30px;
    font-family: "Cinzel", serif;
    font-size: 30px;
    line-height: 1;
    color: var(--black);
    letter-spacing: 1px;
    white-space: nowrap;
  }
  .back__trade {
    position: absolute;
    right: 40px; bottom: 62px;
    font-family: "Arimo", sans-serif;
    font-size: 17px;
    color: var(--white);
  }
</style>
</head>
<body>

<section class="card card--front" aria-label="Card front">
  <div class="front__brand">BQR</div>
  <div class="front__rule"></div>
  <div class="front__band">
    <div class="front__name">Wiremasters Of Northfield, LLC</div>
  </div>
</section>

<section class="card card--back" aria-label="Card back">
  <div class="back__brand">BQR</div>

  <ul class="back__contact">
    <li>240-555-0187
      <svg viewBox="0 0 12 12" aria-hidden="true"><path d="M1 3c0-1 1-2 2-2h1l1 2-1 1c1 2 2 3 4 4l1-1 2 1v1c0 1-1 2-2 2C5 11 1 7 1 3z"/></svg>
    </li>
    <li>Millbrook, MD 20990.
      <svg viewBox="0 0 12 12" aria-hidden="true"><path d="M6 0a4 4 0 0 1 4 4c0 3-4 8-4 8S2 7 2 4a4 4 0 0 1 4-4zm0 2.5a1.5 1.5 0 1 0 0 3 1.5 1.5 0 0 0 0-3z"/></svg>
    </li>
    <li>Dalep@wiremastersnorthfield.example
      <svg viewBox="0 0 12 12" aria-hidden="true"><path d="M0 2h12v8H0z M0 2l6 5 6-5" stroke="#050505" stroke-width="1"/></svg>
    </li>
  </ul>

  <svg class="back__footer" viewBox="0 0 700 130" aria-hidden="true">
    <path d="M0 14 L700 14 L700 20 L0 20 Z" fill="#ffffff"/>
    <path d="M0 20 L430 20 C455 20 470 30 478 48 L478 118 L0 118 Z" fill="#f2dc1e"/>
    <path d="M0 118 L700 118 L700 122 L0 122 Z" fill="#ffffff"/>
    <path d="M0 122 L700 122 L700 130 L0 130 Z" fill="#f2dc1e"/>
  </svg>
  <div class="back__person">Dale Pruitt</div>
  <div class="back__trade">Electricians</div>
</section>

</body>
</html>
```